indépendant en tant que Massothérapeute et Préparateur Mental, j'ai besoin de ...

Massothérapeute et préparateur mental indépendant, je recherche une carte de visite sobre et dynamique, sans images liées au massage ou à la préparation mentale mais intégrant mon logo. Les couleurs que j'aime bien sont : Blanc, gris, anthracite, noir et jaune

Contact Information for Business Card

carte de préférence Horizontale
neutre qui puisse toucher le deux domaines Massothérapie et préparation mentale

Requirements
Must have
• mon projet doit intégrer au recto:
LOGO
Loïc Bardèze
078 513 26 48
info@loicbardeze.ch
et éventuellement www.loicbardeze.ch

et au verso les deux adresses:

Chemin des Ormilles 7B
1400 Yverdon-les-Bains

Route de la Gravière 9
1700 Fribourg

Should not have
• mon projet ne doit pas contenir d'image en liens avec le massage ni la préparation mentale.

```html
<!DOCTYPE html>
<html lang="fr">
<head>
<meta charset="utf-8">
<title>Loïc Bardèze – Carte de visite</title>
<link href="https://fonts.googleapis.com/css2?family=Work+Sans:wght@400;500;600&display=swap" rel="stylesheet">
<style>
  :root {
    --stage: #2b2b2b;
    --anthracite: #3a3939;
    --ink: #1e1e1e;
    --paper: #ffffff;
    --yellow: #f5b915;
    --grey-text: #2a2a2a;
  }
  * { box-sizing: border-box; margin: 0; padding: 0; }
  html, body { width: 1200px; height: 930px; overflow: hidden; }
  body {
    background: var(--stage);
    font-family: "Work Sans", Arial, sans-serif;
    position: relative;
  }
  .card {
    position: absolute;
    width: 520px;
    height: 300px;
    border-radius: 16px;
    overflow: hidden;
  }
  /* Back side */
  .card-back {
    left: 70px; top: 140px;
    background: var(--anthracite);
  }
  .card-back .portrait-area {
    position: absolute;
    left: 130px; top: 40px;
    width: 280px; height: 260px;
    background: radial-gradient(ellipse at 50% 45%, #8a7468 0%, #5a4d48 40%, #3a3939 75%);
  }
  .card-back .brand {
    position: absolute;
    left: 120px; top: 118px;
    color: var(--paper);
  }
  .brand-name {
    font-weight: 600;
    font-size: 30px;
    letter-spacing: 0.5px;
    line-height: 1;
    display: flex;
    align-items: center;
    gap: 10px;
  }
  .brand-mark {
    width: 14px; height: 14px;
    background: currentColor;
    display: inline-block;
  }
  .brand-tagline {
    font-size: 10px;
    letter-spacing: 1px;
    text-transform: uppercase;
    margin-top: 6px;
    margin-left: 24px;
  }
  /* Front side */
  .card-front {
    left: 610px; top: 490px;
    background: var(--paper);
    color: var(--grey-text);
  }
  .card-front .brand {
    position: absolute;
    left: 28px; top: 34px;
    color: var(--ink);
  }
  .card-front .brand-name { font-size: 22px; }
  .card-front .brand-tagline { font-size: 8px; margin-left: 24px; }
  .decor-block {
    position: absolute;
    right: 34px; top: 40px;
    width: 110px; height: 110px;
    background: var(--ink);
  }
  .identity {
    position: absolute;
    left: 28px; top: 104px;
    padding-left: 14px;
    border-left: 5px solid var(--yellow);
  }
  .identity-name {
    color: var(--yellow);
    font-size: 22px;
    font-weight: 500;
    letter-spacing: 0.5px;
    line-height: 1.1;
  }
  .identity-role { font-size: 13px; margin-top: 2px; }
  .contacts {
    position: absolute;
    left: 47px; top: 160px;
    list-style: none;
    font-size: 12.5px;
    line-height: 17px;
  }
  .contacts li { display: flex; align-items: center; gap: 7px; }
  .contacts svg { width: 10px; height: 10px; fill: var(--yellow); flex: none; }
  .addresses {
    position: absolute;
    left: 64px; top: 214px;
    font-size: 12.5px;
    line-height: 17px;
    font-style: normal;
  }
  .addresses p + p { margin-top: 4px; }
</style>
</head>
<body>

<section class="card card-back">
  <div class="portrait-area" role="img" aria-label="Photo d'un enfant posant bras fléchis devant un dessin de bras musclés"></div>
  <div class="brand">
    <div class="brand-name"><span class="brand-mark"></span>Loïc Bardèze</div>
    <div class="brand-tagline">Massothérapeute / Préparateur Mental</div>
  </div>
</section>

<section class="card card-front">
  <div class="brand">
    <div class="brand-name"><span class="brand-mark"></span>Loïc Bardèze</div>
    <div class="brand-tagline">Massothérapeute / Préparateur Mental</div>
  </div>
  <div class="decor-block"></div>

  <div class="identity">
    <div class="identity-name">LOÏC BARDÈZE</div>
    <div class="identity-role">Director</div>
  </div>

  <ul class="contacts">
    <li><svg viewBox="0 0 10 10"><path d="M2 0.5 L3.8 2.8 L2.8 3.8 Q4 6.2 6.2 7.2 L7.2 6.2 L9.5 8 L8 9.6 Q3 9 0.4 2 Z"/></svg>078 513 26 48</li>
    <li><svg viewBox="0 0 10 10"><path d="M0.5 2 H9.5 V8 H0.5 Z M1.5 3 V7 H8.5 V3 L5 5.5 Z" fill-rule="evenodd"/></svg>info@loicbardeze.ch</li>
    <li><svg viewBox="0 0 10 10"><circle cx="5" cy="5" r="4.5"/></svg>www.loicbardeze.ch</li>
  </ul>

  <address class="addresses">
    <p>Chemin des Ormilles 7B<br>1400 Yverdon-les-Bains</p>
    <p>Route de la Gravière 9<br>1700 Fribourg</p>
  </address>
</section>

</body>
</html>
```